Business Card Design

I already have a company logo for my company. I have a logo for the manufacturer we represent. I want a professional business card design.

```html
<!DOCTYPE html>
<html lang="en">
<head>
<meta charset="UTF-8">
<title>Signalguard Co. — Business Card</title>
<link href="https://fonts.googleapis.com/css2?family=Montserrat:wght@400;500;700&display=swap" rel="stylesheet">
<style>
  :root {
    --stage: #2b2b2d;
    --card: #f7f7f7;
    --red: #e3262b;
    --gold: #c9a227;
    --ink: #2a2a2a;
    --muted: #555555;
  }
  * { box-sizing: border-box; margin: 0; padding: 0; }
  html, body { width: 1200px; height: 688px; overflow: hidden; }
  body {
    background: var(--stage);
    font-family: "Montserrat", Arial, sans-serif;
    color: var(--ink);
    position: relative;
  }
  .card {
    position: absolute;
    top: 190px;
    width: 540px;
    height: 309px;
    background: var(--card);
    overflow: hidden;
  }
  .card--front { left: 40px; }
  .card--back { left: 620px; }

  .brand {
    display: flex;
    align-items: center;
    gap: 12px;
    color: var(--red);
    font-weight: 700;
    text-transform: uppercase;
  }
  .brand__square {
    width: 22px; height: 22px;
    background: var(--red);
    flex: none;
  }
  .card--front .brand {
    position: absolute;
    left: 50%; top: 50%;
    transform: translate(-50%, -50%);
    font-size: 34px;
    letter-spacing: 1px;
  }
  .card--back .brand {
    position: absolute;
    left: 32px; top: 44px;
    font-size: 22px;
    letter-spacing: 0.5px;
  }
  .card--back .brand__square { width: 16px; height: 16px; }
  .brand-rule {
    position: absolute;
    left: 32px; top: 78px;
    width: 210px; height: 3px;
    background: var(--gold);
  }

  .mark-area {
    position: absolute;
    right: 0; top: 0;
    width: 220px; height: 190px;
    background: linear-gradient(135deg, #f7f7f7 0%, #f3d9d9 45%, #e9c25a 100%);
  }

  .contact {
    position: absolute;
    left: 32px; top: 120px;
  }
  .contact__name {
    color: var(--red);
    font-weight: 700;
    font-size: 19px;
  }
  .contact__title {
    font-size: 11px;
    color: var(--muted);
    margin-top: 2px;
  }
  .contact__address {
    font-size: 11px;
    line-height: 1.45;
    margin-top: 22px;
  }
  .contact__list {
    list-style: none;
    margin-top: 18px;
    font-size: 11px;
    line-height: 1.7;
  }
  .contact__list li { display: flex; align-items: center; gap: 8px; }
  .contact__list svg { width: 10px; height: 10px; fill: var(--red); flex: none; }
</style>
</head>
<body>
  <section class="card card--front" aria-label="Business card front">
    <div class="brand"><span class="brand__square"></span>Signalguard Co.</div>
  </section>

  <section class="card card--back" aria-label="Business card back">
    <div class="mark-area" role="img" aria-label="Large brand mark decoration area"></div>
    <div class="brand"><span class="brand__square"></span>Signalguard Co.</div>
    <div class="brand-rule"></div>

    <div class="contact">
      <p class="contact__name">Dale Morgan</p>
      <p class="contact__title">Managing Director</p>
      <p class="contact__address">2840 Larkspur Ave<br>Denver, CO 80205</p>
      <ul class="contact__list">
        <li>
          <svg viewBox="0 0 10 10" aria-hidden="true"><path d="M2 0.5 L3.8 2.8 L2.9 3.9 Q4 6 6.1 7.1 L7.2 6.2 L9.5 8 L8.4 9.5 Q4.5 9.3 0.5 1.6 Z"/></svg>
          555.214.0187
        </li>
        <li>
          <svg viewBox="0 0 10 10" aria-hidden="true"><path d="M0.5 2 H9.5 V8 H0.5 Z M0.9 2.4 L5 5.6 L9.1 2.4" stroke="#f7f7f7" stroke-width="0.8"/></svg>
          info@signalguardco.com
        </li>
        <li>
          <svg viewBox="0 0 10 10" aria-hidden="true"><circle cx="5" cy="5" r="4.5"/><path d="M0.5 5 H9.5 M5 0.5 V9.5" stroke="#f7f7f7" stroke-width="0.8"/></svg>
          www.signalguardco.com
        </li>
      </ul>
    </div>
  </section>
</body>
</html>
```